Veltrane Group Business Card Design

The CEO is looking for a new trendy look for his business card.
You can stay with current branding or come up with something new/creative. It can be 3D, including Medical Office buildings. You can use our logo in a variety of colors. Please include name, title, company name, company website, email address, cell number

Target Market(s)

Real Estate Development and Construction

Industry/Entity Type

Health care real estate

Contact Information for Business Card

Rohesh Kamdar, CEO M-604.781.2249 E-roheshkamdar@veltrane.com Address:4180 Lindqvist Ave, Tampa, FL 33482 www.veltrane.com

Font styles to use
Other font styles liked:
• Be creative

Requirements
Must have
• Creative, trendy look
Nice to have
• Please go to our website to get a feel- www. veltrane.com
Should not have
• small fonts

```html
<!DOCTYPE html>
<html lang="en">
<head>
<meta charset="UTF-8">
<title>Veltrane Group Business Card</title>
<link href="https://fonts.googleapis.com/css2?family=Montserrat:wght@300;700&display=swap" rel="stylesheet">
<style>
  :root {
    --backdrop: #2b2b2b;
    --card: #1c1c1c;
    --ink: #ffffff;
    --ink-soft: #e6e6e6;
  }
  * { margin: 0; padding: 0; box-sizing: border-box; }
  html, body {
    width: 1200px;
    height: 1186px;
    overflow: hidden;
    background: var(--backdrop);
    font-family: "Montserrat", sans-serif;
    color: var(--ink);
  }
  .sheet {
    width: 1200px;
    height: 1186px;
    display: flex;
    flex-direction: column;
    align-items: center;
    justify-content: center;
    gap: 60px;
  }
  .card {
    position: relative;
    width: 880px;
    height: 503px;
    background: var(--card);
    box-shadow: 0 10px 30px rgba(0,0,0,0.45);
  }
  .brand {
    position: absolute;
    display: flex;
    align-items: center;
    gap: 18px;
    font-weight: 700;
    color: var(--ink);
    white-space: nowrap;
    line-height: 1;
  }
  .brand__mark {
    flex: none;
    background: var(--ink);
  }
  .card--front .brand {
    left: 50%;
    top: 50%;
    transform: translate(-50%, -50%);
    font-size: 64px;
  }
  .card--front .brand__mark { width: 40px; height: 40px; }
  .card--back .brand {
    right: 60px;
    top: 92px;
    font-size: 44px;
  }
  .card--back .brand__mark { width: 28px; height: 28px; }
  .rule {
    position: absolute;
    left: 60px;
    right: 60px;
    top: 210px;
    height: 1px;
    background: var(--ink-soft);
  }
  .address {
    position: absolute;
    right: 60px;
    top: 232px;
    text-align: right;
    font-style: normal;
    font-weight: 300;
    font-size: 17px;
    line-height: 1.35;
    color: var(--ink-soft);
  }
  .person {
    position: absolute;
    left: 60px;
    bottom: 56px;
    width: 520px;
  }
  .person__name {
    font-weight: 700;
    font-size: 26px;
    letter-spacing: 0.01em;
  }
  .person__title {
    display: flex;
    align-items: center;
    gap: 12px;
    font-weight: 300;
    font-size: 17px;
    margin: 4px 0 18px;
    color: var(--ink-soft);
  }
  .person__title::after {
    content: "";
    flex: 1;
    height: 1px;
    background: var(--ink-soft);
  }
  .contacts { list-style: none; }
  .contacts li {
    display: flex;
    align-items: center;
    gap: 12px;
    font-weight: 300;
    font-size: 18px;
    line-height: 1.7;
    color: var(--ink-soft);
  }
  .contacts svg { width: 16px; height: 16px; fill: var(--ink); flex: none; }
</style>
</head>
<body>
<main class="sheet">
  <section class="card card--front">
    <div class="brand">
      <span class="brand__mark" aria-hidden="true"></span>
      <span class="brand__name">Veltrane Group</span>
    </div>
  </section>

  <section class="card card--back">
    <div class="brand">
      <span class="brand__mark" aria-hidden="true"></span>
      <span class="brand__name">Veltrane Group</span>
    </div>
    <div class="rule"></div>
    <address class="address">
      4180 Lindqvist Ave,<br>Tampa, FL 33482
    </address>
    <div class="person">
      <h1 class="person__name">Rohesh Kamdar</h1>
      <p class="person__title">CEO</p>
      <ul class="contacts">
        <li>
          <svg viewBox="0 0 24 24" aria-hidden="true"><path d="M6.6 10.8a15.1 15.1 0 0 0 6.6 6.6l2.2-2.2a1 1 0 0 1 1-.25 11.4 11.4 0 0 0 3.6.57 1 1 0 0 1 1 1V20a1 1 0 0 1-1 1A17 17 0 0 1 3 4a1 1 0 0 1 1-1h3.5a1 1 0 0 1 1 1c0 1.25.2 2.45.57 3.57a1 1 0 0 1-.25 1z"/></svg>
          604.781.2249
        </li>
        <li>
          <svg viewBox="0 0 24 24" aria-hidden="true"><path d="M2 5h20v14H2z M2 5l10 7 10-7" fill="none" stroke="#fff" stroke-width="2"/><path d="M2 5h20L12 12z"/></svg>
          roheshkamdar@veltrane.com
        </li>
        <li>
          <svg viewBox="0 0 24 24" aria-hidden="true"><circle cx="12" cy="12" r="9" fill="none" stroke="#fff" stroke-width="2"/><path d="M3 12h18M12 3c3 3 3 15 0 18M12 3c-3 3-3 15 0 18" fill="none" stroke="#fff" stroke-width="1.6"/></svg>
          www.veltrane.com
        </li>
      </ul>
    </div>
  </section>
</main>
</body>
</html>
```